VOMRA Pty Ltd Business Card

Looking for a simple yet eye-catching double-sided business card design using my company logo on one side and contact details on the other.

Target Market(s)

Government

Industry/Entity Type

Communication Systems Engineering

Contact Information for Business Card

VOMRA Pty Ltd

Requirements
Nice to have
• Would be great to have a QR code so details can be scanned into contacts

```html
<!DOCTYPE html>
<html lang="en">
<head>
<meta charset="utf-8">
<title>VOMRA Pty Ltd Business Card</title>
<link href="https://fonts.googleapis.com/css2?family=Open+Sans:wght@400;700&display=swap" rel="stylesheet">
<style>
  :root {
    --backdrop: #2b2e31;
    --card: #ffffff;
    --slate: #2f3a40;
    --ink: #1f2428;
  }
  * { box-sizing: border-box; margin: 0; padding: 0; }
  html, body { width: 1200px; height: 780px; overflow: hidden; }
  body {
    background: var(--backdrop);
    font-family: "Open Sans", Arial, sans-serif;
    display: flex;
    align-items: center;
    justify-content: center;
    gap: 50px;
  }
  .card {
    position: relative;
    width: 540px;
    height: 310px;
    background: var(--card);
    border-radius: 20px;
    overflow: hidden;
    box-shadow: 0 14px 30px rgba(0,0,0,.45);
  }
  .edge-band {
    position: absolute;
    left: 0; right: 0; bottom: 0;
    height: 22px;
  }
  .wordmark {
    color: var(--slate);
    font-weight: 700;
    letter-spacing: 2px;
    line-height: 1;
  }
  /* back: contact side */
  .back .wordmark {
    position: absolute;
    left: 46px; top: 92px;
    font-size: 54px;
  }
  .divider {
    position: absolute;
    left: 262px; top: 70px;
    width: 1.5px; height: 140px;
    background: var(--ink);
  }
  .person {
    position: absolute;
    left: 290px; top: 62px;
    color: var(--slate);
  }
  .person-name { font-size: 27px; font-weight: 700; line-height: 1.1; }
  .person-role { font-size: 15px; color: var(--ink); margin-bottom: 10px; }
  .contact-list { list-style: none; font-size: 17px; color: var(--ink); line-height: 1.45; }
  .contact-list li { display: flex; align-items: center; gap: 8px; }
  .contact-list svg { width: 15px; height: 15px; flex: none; }
  .address {
    position: absolute;
    left: 46px; bottom: 40px;
    font-size: 15.5px;
    color: var(--ink);
  }
  /* front: logo side */
  .front .brand {
    position: absolute;
    inset: 0 0 22px 0;
    display: flex;
    align-items: center;
    justify-content: center;
    gap: 18px;
  }
  .front .wordmark { font-size: 84px; }
  .brand-dot {
    width: 46px; height: 46px;
    border-radius: 50%;
    background: var(--slate);
  }
</style>
</head>
<body>

  <section class="card back" aria-label="Contact side">
    <div class="wordmark">VOMRA</div>
    <div class="divider"></div>
    <div class="person">
      <div class="person-name">Jordan Hale</div>
      <div class="person-role">Co-Founder</div>
      <ul class="contact-list">
        <li>
          <svg viewBox="0 0 16 16" aria-hidden="true"><path fill="#2f3a40" d="M3.5 1.5l2.5 0 1 3.5-1.7 1.2a8 8 0 0 0 4.5 4.5L11 9l3.5 1v2.5c0 1-1 2-2 2A11 11 0 0 1 1.5 3.5c0-1 1-2 2-2z"/></svg>
          (555) 014-2287
        </li>
        <li>
          <svg viewBox="0 0 16 16" aria-hidden="true"><circle cx="8" cy="8" r="6.5" fill="none" stroke="#2f3a40" stroke-width="1.6"/><path d="M1.5 8h13M8 1.5c-3 3.5-3 9.5 0 13M8 1.5c3 3.5 3 9.5 0 13" fill="none" stroke="#2f3a40" stroke-width="1.2"/></svg>
          www.vomra.com.au
        </li>
        <li>
          <svg viewBox="0 0 16 16" aria-hidden="true"><rect x="1" y="3" width="14" height="10" rx="1.5" fill="#2f3a40"/><path d="M1.5 4l6.5 5 6.5-5" fill="none" stroke="#fff" stroke-width="1.3"/></svg>
          admin@vomra.com.au
        </li>
      </ul>
    </div>
    <p class="address">14-16 Harlow Street Ashfield NSW 2131 Australia</p>
    <svg class="edge-band" viewBox="0 0 540 22" preserveAspectRatio="none" aria-hidden="true">
      <polygon points="0,0 150,0 140,22 0,22" fill="#2f3a40"/>
      <polygon points="166,0 540,0 540,22 156,22" fill="#2f3a40"/>
    </svg>
  </section>

  <section class="card front" aria-label="Logo side">
    <div class="brand">
      <span class="brand-dot" aria-hidden="true"></span>
      <span class="wordmark">VOMRA</span>
    </div>
    <svg class="edge-band" viewBox="0 0 540 22" preserveAspectRatio="none" aria-hidden="true">
      <polygon points="0,0 300,0 290,22 0,22" fill="#2f3a40"/>
      <polygon points="316,0 540,0 540,22 306,22" fill="#2f3a40"/>
    </svg>
  </section>

</body>
</html>
```